Pet sitting Business needs a website

We need a website that shows our services and prices. Shows our love of animals but also our professionalism. want a gallery, about, blog, services, links to fb and instagram accounts, newsletter archive. want it to be easy to access and wonderful to navigate. want the domain to be Birchfordpawhaven.com
take any info from FB site www.facebook.com/birchfordpawhaven
I would like it to fit square space platform

Target Market(s)

upscale area, responsible pet owners,

Industry/Entity Type

Pet Care

Coding

Coded - Design and coding required

Number of Pages Required

5+ page

Font styles to use
Sans Serif

Requirements
Must have
• (square space platform)
• Menu
• photo gallery
• about us
• services
• policies
• monthly newsletter
• unavailable dates
• Introduction (welcome)
• payment methods
• Daily updates
• testimonials (use from fb site)
Should not have
• stock photos

```html
<!DOCTYPE html>
<html lang="en">
<head>
<meta charset="utf-8">
<title>Birchford Paw Haven</title>
<link rel="stylesheet" href="https://fonts.googleapis.com/css2?family=Roboto:ital,wght@0,400;0,500;0,700;1,400&family=Open+Sans:wght@400;600;700&display=swap">
<style>
:root{
  --blue:#1a7fc0;
  --blue-dark:#0f6aa6;
  --blue-light:#4ab5e0;
  --orange:#dc9a0c;
  --orange-dark:#c88800;
  --ink:#1d1d1d;
  --text:#555;
  --grey-bg:#efefef;
  --footer:#141414;
  --white:#fff;
}
*{box-sizing:border-box;margin:0;padding:0}
html,body{width:1200px;height:2894px;overflow:hidden;background:var(--white)}
body{position:relative;font-family:'Open Sans',sans-serif;color:var(--text);font-size:12px;line-height:1.9}
.abs{position:absolute}
h2{font-family:'Roboto',sans-serif;font-weight:500;color:var(--ink);font-size:27px;letter-spacing:.5px}

/* top bar */
.top-line{left:0;top:0;width:1200px;height:7px;background:var(--orange)}
.tab{top:0;height:36px;background:var(--orange);color:var(--white);font-family:'Roboto',sans-serif;display:flex;align-items:center;justify-content:center}
.tab-call{left:546px;width:200px;font-size:15px;clip-path:polygon(0 0,100% 0,93% 100%,7% 100%)}
.tab-dates{left:758px;width:442px;font-size:11px;clip-path:polygon(0 0,100% 0,100% 100%,4% 100%)}
.tab b{font-weight:700;margin-right:4px}

/* header */
.brand{left:96px;top:56px;display:flex;align-items:center;gap:10px}
.brand-dot{width:34px;height:34px;border-radius:50%;background:var(--orange)}
.brand-name{font-family:'Open Sans',sans-serif;font-weight:600;color:var(--orange);font-size:20px;line-height:1.1;width:140px}
.nav{left:372px;top:82px;display:flex;gap:22px;font-family:'Roboto',sans-serif;font-size:12px;color:var(--ink);font-weight:500}
.nav .active{color:var(--blue);position:relative}
.nav .active::after{content:"";position:absolute;left:-10px;right:-10px;top:30px;height:5px;background:var(--blue)}

/* hero */
.hero-band{left:0;top:212px;width:1200px;height:405px;background:linear-gradient(180deg,var(--blue) 0%,var(--blue-dark) 100%)}
.hero-frame{left:96px;top:150px;width:1008px;height:414px;background:var(--white);box-shadow:0 4px 12px rgba(0,0,0,.25);padding:4px}
.hero-photo{width:100%;height:100%;background:linear-gradient(100deg,#d9d6d0 0%,#ece9e3 45%,#c9954f 70%,#a86d2e 100%)}
.hero-title{left:100px;top:282px;width:340px;height:46px;background:rgba(25,25,25,.88);color:var(--orange);font-family:'Roboto',sans-serif;font-size:23px;letter-spacing:1px;padding:7px 24px}
.hero-text{left:100px;top:334px;width:480px;height:78px;background:rgba(25,25,25,.82);color:var(--white);font-size:14px;line-height:1.7;padding:12px 24px}
.dots{left:120px;top:432px;display:flex;gap:12px}
.dots span{width:12px;height:12px;border-radius:50%;background:#222}
.dots span:first-child{background:var(--blue)}

/* welcome */
.welcome{left:120px;top:655px;width:960px;text-align:center}
.welcome h2{margin-bottom:12px}
.welcome p{font-size:11px;line-height:2.6}
.welcome p+p{margin-top:10px}
.rule{left:98px;top:887px;width:1004px;height:1px;background:#e3e3e3}

/* gallery */
.gallery-title{left:98px;top:925px}
.arrows{display:flex;gap:10px;color:#aaa;font-size:16px}
.gallery-arrows{left:688px;top:932px}
.gallery{left:98px;top:986px;width:616px;height:299px;display:grid;grid-template-columns:repeat(3,1fr);grid-template-rows:repeat(2,1fr);gap:3px}
.ph{display:block}
.ph1{background:linear-gradient(135deg,#6b5a48,#a8937a)}
.ph2{background:linear-gradient(135deg,#3a3a3a,#bdbdbd)}
.ph3{background:linear-gradient(135deg,#b88d5a,#e0cbb0)}
.ph4{background:linear-gradient(135deg,#3f7a3a,#c8a07a)}
.ph5{background:linear-gradient(135deg,#6f8a5a,#8d7d6a)}
.ph6{background:linear-gradient(135deg,#4a3b4a,#b59a86)}

/* newsletter */
.newsletter{left:756px;top:936px;width:346px;height:353px;background:var(--orange);padding:12px 16px;box-shadow:0 3px 8px rgba(0,0,0,.2)}
.newsletter h3{font-family:'Roboto',sans-serif;font-weight:500;color:var(--white);font-size:27px;letter-spacing:.5px;margin-bottom:12px}
.field{background:var(--white);border-radius:3px;height:40px;margin:0 0 6px;padding:8px 14px;font-size:10px;color:#888}
.field-tall{height:74px}
.subscribe{margin-top:4px;height:40px;border-radius:3px;background:linear-gradient(180deg,#2b8fc9,#0d5c8c);color:var(--white);font-family:'Roboto',sans-serif;font-weight:700;font-size:13px;text-align:center;line-height:40px}

/* testimonials */
.testi-band{left:0;top:1337px;width:1200px;height:313px;background:linear-gradient(180deg,var(--blue-light) 0%,var(--blue) 100%)}
.testi-title{left:0;top:1388px;width:1200px;text-align:center;color:var(--white)}
.testi-arrows{left:1060px;top:1396px;display:flex;gap:8px}
.testi-arrows span{width:16px;height:16px;border-radius:50%;background:rgba(255,255,255,.7)}
.avatar{border-radius:50%;border:5px solid var(--white);box-shadow:0 2px 8px rgba(0,0,0,.3)}
.testi-avatar{left:130px;top:1456px;width:140px;height:140px;background:linear-gradient(135deg,#caa07a,#7a5a3e)}
.quote{left:305px;top:1452px;width:790px;color:var(--white);font-style:italic;font-family:'Roboto',sans-serif;font-size:12px;line-height:2.55}
.qmark{font-size:34px;font-weight:700;font-style:normal;line-height:0;vertical-align:-10px;margin:0 6px}
.quote-by{left:305px;top:1558px;color:var(--white);font-family:'Roboto',sans-serif;font-size:15px}
.quote-by b{font-weight:700}
.quote-by i{font-size:13px}

/* services */
.services-title{left:0;top:1685px;width:1200px;text-align:center}
.service{width:300px;display:flex;gap:18px}
.icon{flex:0 0 62px;height:62px;border-radius:50%;border:2px solid var(--blue);display:flex;align-items:center;justify-content:center}
.icon.solid{background:var(--blue)}
.service h4{font-family:'Roboto',sans-serif;font-weight:500;color:var(--orange);font-size:14px;line-height:1.3}
.service .price{font-family:'Roboto',sans-serif;color:var(--blue-dark);font-size:15px;font-weight:500;line-height:1.9}
.service .price small{color:#333;font-weight:400;font-size:12px}
.service p{font-size:11px;line-height:2}

/* about + policies */
.warm-band{left:0;top:2016px;width:1200px;height:395px;background:var(--orange)}
.warm-band h2{color:var(--white)}
.about-title{left:98px;top:2054px}
.about-photo{left:98px;top:2112px;width:232px;height:232px;border-width:6px;background:linear-gradient(135deg,#e8c8a0,#8a6440)}
.about-text{left:351px;top:2102px;width:235px;color:var(--white);font-size:11.5px;line-height:2}
.more{display:block;margin-top:6px;color:#2a4f6a;text-decoration:underline;font-size:11px}
.pol-title{left:627px;top:2054px}
.pol-arrows{left:1064px;top:2064px}
.policies{left:627px;top:2104px;width:470px;color:var(--white);font-size:11.5px;line-height:2}
.policies h5{font-family:'Roboto',sans-serif;font-weight:700;color:#fff3c8;font-size:13px;margin-bottom:2px}
.policies h5::before{content:"";display:inline-block;width:10px;height:10px;border-radius:50%;border:2px solid #fff3c8;margin-right:7px;vertical-align:-1px}
.policies .item+.item{margin-top:16px}

/* news */
.news-band{left:0;top:2411px;width:1200px;height:342px;background:var(--grey-bg)}
.news-title{left:0;top:2459px;width:1200px;text-align:center}
.news-photo{left:208px;top:2494px;width:220px;height:220px;border-width:6px;background:linear-gradient(135deg,#d4a880,#5a3e2c)}
.news-body{left:432px;top:2526px;width:614px}
.news-body h4{font-family:'Roboto',sans-serif;font-weight:700;color:var(--blue);font-size:13px}
.news-date{color:var(--orange);font-size:12px;margin:6px 0 4px}
.news-body p{font-size:11.5px;line-height:2.25}
.chev{top:2590px;font-size:40px;color:#c9c9c9;font-family:'Roboto',sans-serif;font-weight:400}

/* footer */
.footer{left:0;top:2753px;width:1200px;height:141px;background:var(--footer)}
.social{left:0;top:2773px;width:1200px;display:flex;justify-content:center;gap:10px}
.social span{width:32px;height:32px;border-radius:50%;border:2px solid #888}
.foot-links{left:0;top:2818px;width:1200px;text-align:center;color:#aaa;font-size:11px}
.foot-links span{margin:0 6px}
.copy{left:0;top:2840px;width:1200px;text-align:center;color:#888;font-size:11px}
</style>
</head>
<body>

<div class="abs top-line"></div>
<div class="abs tab tab-call">Call Us:&nbsp; 555-014-2290</div>
<div class="abs tab tab-dates"><b>UNAVAILABLE DATES :</b> May 6-8th MAY 21-23 July 3-16</div>

<div class="abs brand"><span class="brand-dot"></span><span class="brand-name">Birchford Paw Haven</span></div>
<nav class="abs nav">
  <span class="active">Home</span><span>Photo Gallery</span><span>About us</span><span>Services</span><span>Policies</span><span>Monthly Newsletter</span><span>Unavailable Dates</span><span>Introduction</span><span>Payment Methods</span>
</nav>

<div class="abs hero-band"></div>
<div class="abs hero-frame"><div class="hero-photo" role="img" aria-label="Golden retriever lying beside a grey cat on a bright floor"></div></div>
<div class="abs hero-title">BIRCHFORD PAW HAVEN CLUB</div>
<div class="abs hero-text">Excepteur sint occaecat cupidatat non proident, sunt in culpa officia deserunt mollit anim tempora incidunt...</div>
<div class="abs dots"><span></span><span></span><span></span></div>

<section class="abs welcome">
  <h2>WELCOME TO BIRCHFORD PAW HAVEN</h2>
  <p>The biggest key is to make people aware that I was a Licensed Veterinarian Technician from Nashville, Tn. That is a huge "selling" point when hiring someone to care for your pets<br>
  Instead of feeling guilty when you must leave your pet for long work days, travel or appointments you can feel good knowing that you have provided your pet with a best friend,<br>
  Birchford Paw Haven. Birchford Paw Haven provides your pet with one on one attention, plenty of play time...</p>
  <p>Exercise and lots and lots of love until your return. I, pets do better and have less stress when they remain in their own homes where the sites, sounds and smells are familiar.<br>
  They feel safe and comfortable. While you are away there is no need to expose your pet to other pets and possible illness associated with kennels.</p>
</section>
<div class="abs rule"></div>

<h2 class="abs gallery-title">PHOTO GALLERY</h2>
<div class="abs arrows gallery-arrows"><span>&#8249;</span><span>&#8250;</span></div>
<div class="abs gallery">
  <span class="ph ph1" role="img" aria-label="Tabby kitten looking at the camera"></span>
  <span class="ph ph2" role="img" aria-label="Black and white photo of a dog resting"></span>
  <span class="ph ph3" role="img" aria-label="Small tan dog on a lap"></span>
  <span class="ph ph4" role="img" aria-label="Owner holding a pug outdoors"></span>
  <span class="ph ph5" role="img" aria-label="Cats eating from bowls on a wooden deck"></span>
  <span class="ph ph6" role="img" aria-label="Owner with a small dog indoors"></span>
</div>

<aside class="abs newsletter">
  <h3>NEWSLETTER</h3>
  <div class="field">FIRST NAME*</div>
  <div class="field">LAST NAME*</div>
  <div class="field">E-MAIL*</div>
  <div class="field field-tall">DETAILS*</div>
  <div class="subscribe">SUBSCRIBE</div>
</aside>

<div class="abs testi-band"></div>
<h2 class="abs testi-title" style="color:var(--white)">TESTIMONIALS</h2>
<div class="abs testi-arrows"><span></span><span></span></div>
<div class="abs avatar testi-avatar" role="img" aria-label="Client portrait with her cat"></div>
<p class="abs quote"><span class="qmark">&ldquo;</span>Sed ut perspiciatis unde omnis iste natus error sit voluptatem accusantium doloremque laudantium, totam rem aperiam, eaque ipsa quae ab illo inventore veritatis et quasi architecto beatae vitae dicta sunt explicaboi mpsam voluptatem quia voluptas sit aspernatur out odit aut fugit, sed quia consequuntur magni ullam corporis suscipit laboriosam, nisi ut aliquid ex ea commodi nostrum exercitationem...<span class="qmark">&rdquo;</span></p>
<div class="abs quote-by"><b>-CLARA BENTON,</b> <i>City Name, Lorem sipmdl</i></div>

<h2 class="abs services-title">SERVICES</h2>

<div class="abs service" style="left:98px;top:1746px">
  <div class="icon solid"><svg width="30" height="30" viewBox="0 0 30 30"><circle cx="15" cy="15" r="11" fill="none" stroke="#fff" stroke-width="3"/><path d="M15 9v7h5" fill="none" stroke="#fff" stroke-width="3"/></svg></div>
  <div><h4>DAILY VISIT</h4><div class="price">$25.00 <small>(per visit)</small></div><p>Sed ut perspiciatis unde omnis iste nater laudantium, totam rem aperiam...</p></div>
</div>
<div class="abs service" style="left:457px;top:1746px">
  <div class="icon"><svg width="28" height="28" viewBox="0 0 28 28" fill="none" stroke="#1a7fc0" stroke-width="3"><path d="M4 4l7 7M24 4l-7 7M4 24l7-7M24 24l-7-7M4 4h6M4 4v6M24 4h-6M24 4v6M4 24h6M4 24v-6M24 24h-6M24 24v-6"/></svg></div>
  <div><h4>JUST WALKS</h4><div class="price">$15.00/ 20 <small>-min walk</small></div><p>Sed ut perspiciatis unde omnis iste nater laudantium, totam rem aperiam...</p></div>
</div>
<div class="abs service" style="left:812px;top:1746px">
  <div class="icon"><svg width="32" height="22" viewBox="0 0 32 22"><path d="M2 11Q16-4 30 11Q16 26 2 11Z" fill="none" stroke="#1a7fc0" stroke-width="3"/><circle cx="16" cy="11" r="4.5" fill="#1a7fc0"/></svg></div>
  <div><h4>POTTY VISITS</h4><div class="price">$10.00</div><p>Sed ut perspiciatis unde omnis iste nater laudantium, totam rem aperiam...</p></div>
</div>
<div class="abs service" style="left:98px;top:1874px">
  <div class="icon"><svg width="30" height="24" viewBox="0 0 30 24" fill="#1a7fc0"><path d="M6 4h18l4 8v9h-4v-3H6v3H2v-9z"/><rect x="8" y="6" width="14" height="5" fill="#fff"/><circle cx="8" cy="14" r="2" fill="#fff"/><circle cx="22" cy="14" r="2" fill="#fff"/></svg></div>
  <div><h4>PET TAXI</h4><div class="price">$10.00 <small>(each trip)</small></div><p>Sed ut perspiciatis unde omnis iste nater laudantium, totam rem aperiam...</p></div>
</div>
<div class="abs service" style="left:457px;top:1874px">
  <div class="icon"><svg width="28" height="26" viewBox="0 0 28 26"><rect x="2" y="6" width="24" height="18" rx="3" fill="none" stroke="#1a7fc0" stroke-width="3"/><path d="M10 6V2h8v4M14 10v10M9 15h10" stroke="#1a7fc0" stroke-width="3" fill="none"/></svg></div>
  <div><h4>MEDICATION</h4><div class="price">$5.00 <small>(peradministration)</small></div><p>Sed ut perspiciatis unde omnis iste nater laudantium, totam rem aperiam...</p></div>
</div>
<div class="abs service" style="left:812px;top:1874px">
  <div class="icon"><svg width="28" height="26" viewBox="0 0 28 26" fill="#1a7fc0"><path d="M14 2L1 13h4v11h7v-7h4v7h7V13h4z"/></svg></div>
  <div><h4>DOG PARK</h4><div class="price">$40.00 <small>(30 min of play)</small></div><p>Sed ut perspiciatis unde omnis iste nater laudantium, totam rem aperiam...</p></div>
</div>

<div class="abs warm-band"></div>
<h2 class="abs about-title">ABOUT US</h2>
<div class="abs avatar about-photo" role="img" aria-label="Owner smiling with her golden dog"></div>
<div class="abs about-text">Hi my name is Maren Holloway and Iwould love to introduce myself. I am a Licensed Veterinarian Technician from Nashville, Tennessee. My family and I moved to San Antonio in 2008.<br><br>I have dedicated the last 13 years to raising my 2 beautiful children and 5 of my furry babies.I have the knowledge and the training to give the special care your pet will need. I was a Licensed Veterinarian...<a class="more">Read More Info</a></div>
<h2 class="abs pol-title">POLICIES</h2>
<div class="abs arrows pol-arrows"><span style="color:#fff">&#9664;</span><span style="color:#fff">&#9654;</span></div>
<div class="abs policies">
  <div class="item"><h5>CONSULTATION VISIT</h5>You will receive a free visit consultation from Birchford Paw Haven to meet you and your pet. During this visit we will discuss all important issues with you and can help you fill out the necessary documents. This is the time to provide Birchford Paw Haven....<a class="more">Read More Info</a></div>
  <div class="item"><h5>CONSULTATION VISIT</h5>You will receive a free visit consultation from Birchford Paw Haven to meet you and your pet. During this visit we will discuss all important issues with you and can help you fill out the necessary documents. This is the time to provide Birchford Paw Haven....<a class="more">Read More Info</a></div>
</div>

<div class="abs news-band"></div>
<h2 class="abs news-title">CLUB NEWS</h2>
<div class="abs chev" style="left:96px">&#8249;</div>
<div class="abs chev" style="left:1086px">&#8250;</div>
<div class="abs avatar news-photo" role="img" aria-label="Owner holding a small dog"></div>
<article class="abs news-body">
  <h4>LOREM IPSUM ES SIMPLEMENTE EL TEXTO DE RELLENO DE LAS...</h4>
  <div class="news-date">Posted on 27 July 2016</div>
  <p>Lorem Ipsum es simplemente el texto de relleno de las imprentas y archivos de texto. Lorem Ipsum ha sido dedica a la imprenta) desconocido usó una galería de textos y los mezcló de tal manera que logró hacer un libro de textos especimen.No sólo sobrevivió 500 años, sino que tambien ingresó como texto de relleno en documentos electrónicos, quedando esencialmente igual al original...</p>
</article>

<footer class="abs footer"></footer>
<div class="abs social"><span></span><span></span><span></span><span></span><span></span></div>
<div class="abs foot-links"><span>Home</span>|<span>Photo Gallery</span>|<span>About us</span>|<span>Services</span>|<span>Policies</span>|<span>Monthly Newsletter</span>|<span>Unavailable Dates</span>|<span>Introduction</span>|<span>Payment Methods</span></div>
<div class="abs copy">&copy;2016,birchfordpawhaven | Allrights Reserved.</div>

</body>
</html>
```